Business card design needed

Our company background is that we provides transfers to and from the airport, social & corporate events, weddings.
We are also available for charter for birthday party, wine tastings, concerts, anniversary, school balls etc.
Our business cards have to reflect that we have a professional company, they are our first contact and have to stand out from the other 'players' in the market.

Industry/Entity Type

School

Contact Information for Business Card

TELVIK BDR, Lorcan & Mirabel, mob: 0428 351 972, PO Box 847, Dunmere TS 6971, ABN 52 714 309 268, Lic 7164/2918,

Requirements
Must have
• Telephone number: 0428 351 972
Website: www.TELVIKBDR.com.au
postal address: PO Box 847, Dunmere TS 6971
Licences: Lic 7164/2918

***If using the new photo (one with the bus and buildings behind it), if possible can the buildings be cropped out. Thanks
Nice to have
• would be nice to have the pics of the vehicle(s), preferred the Vorn on the card but not too fussed.
Should not have
• Picture of vehicle we don't have in our fleet. (We ONLY have the Vornelles and Korimu Daltra mini bus)

```html
<!DOCTYPE html>
<html lang="en">
<head>
<meta charset="utf-8">
<title>Telvik Luxury Car &amp; Coach – Business Card</title>
<link rel="stylesheet" href="https://fonts.googleapis.com/css2?family=Comfortaa:wght@400;600&family=Roboto+Condensed:wght@300;400;700&display=swap">
<style>
  :root {
    --navy: #0f3a55;
    --sky: #2f9fd3;
    --white: #ffffff;
    --silver-light: #dcdcd6;
    --silver-dark: #7d7f7c;
    --van-light: #e9edef;
    --van-dark: #8d9aa3;
  }
  * { margin: 0; padding: 0; box-sizing: border-box; }
  html, body { width: 1200px; height: 742px; overflow: hidden; background: var(--navy); }
  .card {
    position: relative;
    width: 1200px;
    height: 742px;
    overflow: hidden;
    background: var(--navy);
  }
  .band-line {
    position: absolute;
    left: 0;
    width: 1200px;
    height: 7px;
    background: var(--sky);
  }
  .band-line.top { top: 62px; }
  .band-line.bottom { top: 296px; }
  .brand-band {
    position: absolute;
    left: 0;
    top: 69px;
    width: 1200px;
    height: 227px;
    background: var(--white);
  }
  .brand {
    position: absolute;
    left: 82px;
    top: 78px;
    color: var(--navy);
    font-family: "Comfortaa", sans-serif;
  }
  .brand-name {
    font-size: 148px;
    font-weight: 600;
    line-height: 1;
    letter-spacing: 4px;
  }
  .brand-tagline {
    margin-top: 8px;
    font-size: 44px;
    font-weight: 400;
    line-height: 1;
  }
  .photo { position: absolute; }
  .photo.sedan {
    left: 616px;
    top: 0;
    width: 551px;
    height: 356px;
    background: linear-gradient(180deg, var(--silver-light) 0%, #bfc0ba 55%, var(--silver-dark) 100%);
    border-radius: 60px 60px 24px 24px;
  }
  .photo.minibus {
    left: 0;
    top: 346px;
    width: 486px;
    height: 396px;
    background: linear-gradient(160deg, var(--van-light) 0%, #cfd6da 55%, var(--van-dark) 100%);
    border-radius: 0 70px 0 0;
  }
  .contact {
    position: absolute;
    right: 48px;
    top: 424px;
    text-align: right;
    color: var(--white);
    font-family: "Roboto Condensed", sans-serif;
    line-height: 54px;
    white-space: nowrap;
  }
  .contact-names { font-size: 46px; font-weight: 400; letter-spacing: 0.5px; }
  .contact-phone { font-size: 48px; font-weight: 700; letter-spacing: 2px; }
  .contact-web { font-size: 47px; font-weight: 700; letter-spacing: 1px; }
  .contact-post { font-size: 47px; font-weight: 400; letter-spacing: 1px; }
  .contact-licence { font-size: 40px; font-weight: 400; letter-spacing: 1px; }
</style>
</head>
<body>
  <div class="card">
    <div class="band-line top"></div>
    <div class="brand-band"></div>
    <div class="band-line bottom"></div>

    <div class="brand">
      <div class="brand-name">Telvik</div>
      <div class="brand-tagline">Luxury Car &amp; Coach</div>
    </div>

    <div class="photo sedan" role="img" aria-label="Photo of the silver Vornelle luxury sedan, front view"></div>
    <div class="photo minibus" role="img" aria-label="Photo of the white Korimu Daltra mini bus, front three-quarter view"></div>

    <div class="contact">
      <p class="contact-names">Lorcan &amp; Mirabel</p>
      <p class="contact-phone">0428 351 972</p>
      <p class="contact-web">www.TELVIKBDR.com.au</p>
      <p class="contact-post">PO Box 847, Dunmere TS 6971</p>
      <p class="contact-licence">Lic 7164/2918</p>
    </div>
  </div>
</body>
</html>
```